Spring Detox sale graphics for social media

You MUST read the Brief in the WORD document and follow the instructions there. I want to create 10 social media graphics (new Instagram size 4:5 (1080 x 1350 pixels) focusing on our Mother’s Day Spring Detox Sale graphics, using any of the pics attached. Use the attached pics, NO RANDOM STOCK PHOTOGRAPHY. For the color scheme of the graphics, they should all be complementary to the product colors or feel like Spring time.

Target Market(s)

primarily women

Requirements
Must have
• the photos and text attached

```html
<!DOCTYPE html>
<html lang="en">
<head>
<meta charset="utf-8">
<title>Mother's Day Spring Detox Sale – Social Set</title>
<link href="https://fonts.googleapis.com/css2?family=Bebas+Neue&family=Archivo+Black&family=Montserrat:wght@800&family=Poppins:wght@600;700&display=swap" rel="stylesheet">
<style>
  :root{
    --board:#59595b;
    --white:#ffffff;
    --rose:#f25c8f;
    --hot:#f0086b;
    --blush:#ffd1df;
    --petal:#f8a3c2;
    --bottle-a:#f7f6f8;
    --bottle-b:#dcdade;
  }
  html,body{margin:0;padding:0;overflow:hidden}
  body{width:1200px;height:3484px;background:var(--board);position:relative}
  .post{position:absolute;width:494px;height:617px;overflow:hidden;background:var(--white)}
  .col-a{left:88px}.col-b{left:630px}
  .row-1{top:107px}.row-2{top:766px}.row-3{top:1425px}.row-4{top:2084px}.row-5{top:2743px}
  .line{position:absolute;left:0;right:0;text-align:center;line-height:1;white-space:nowrap;font-family:'Bebas Neue',sans-serif}
  .wide{font-family:'Archivo Black',sans-serif}
  .round{font-family:'Poppins',sans-serif;font-weight:700}
  .heavy{font-family:'Montserrat',sans-serif;font-weight:800}
  .rose{color:var(--rose)}.hot{color:var(--hot)}.light{color:var(--white)}
  .rule{position:absolute;height:5px;background:var(--hot)}
  .block{position:absolute}
  .products{position:absolute;background:linear-gradient(180deg,var(--bottle-a) 0%,var(--bottle-b) 100%);border-radius:10px}
  .photo{position:absolute}
  .left-align{text-align:left;right:auto}
  .right-align{text-align:right;left:auto}
  .tri{position:absolute;left:0;top:0}
</style>
</head>
<body>

<!-- Post 1 -->
<section class="post col-a row-1">
  <div class="line rose" style="top:29px;font-size:126px">MOTHER’S</div>
  <div class="rule" style="left:0;width:158px;top:196px;background:var(--hot)"></div>
  <div class="rule" style="left:336px;width:158px;top:196px;background:var(--hot)"></div>
  <div class="line rose" style="top:141px;font-size:126px">DAY</div>
  <div class="line rose" style="top:248px;font-size:126px">SPRING</div>
  <div class="line rose" style="top:355px;font-size:116px">DETOX SALE</div>
  <div class="block" style="left:0;top:475px;width:142px;height:120px;background:var(--petal);border-radius:0 30px 30px 0"></div>
  <div class="block" style="left:4px;top:491px;width:488px;height:76px;background:var(--hot);border-radius:38px"></div>
  <div class="line light" style="top:503px;font-size:60px">25% OFF EVERYTHING!</div>
</section>

<!-- Post 2 -->
<section class="post col-b row-1">
  <div class="rule" style="left:0;width:120px;top:67px;background:var(--rose)"></div>
  <div class="rule" style="left:372px;width:122px;top:67px;background:var(--rose)"></div>
  <div class="line hot" style="top:34px;font-size:81px">25% OFF</div>
  <div class="line rose" style="top:112px;font-size:81px">MOTHER’S DAY</div>
  <div class="line hot" style="top:251px;font-size:97px">SPRING DETOX</div>
  <div class="line rose" style="top:340px;font-size:97px">SALE</div>
  <div class="block" style="left:35px;top:478px;width:407px;height:132px;background:var(--hot);border-radius:66px"></div>
  <div class="products" role="img" aria-label="Four supplement bottles in a row" style="left:73px;top:441px;width:332px;height:139px"></div>
</section>

<!-- Post 3 -->
<section class="post col-a row-2">
  <div class="photo" role="img" aria-label="Smiling woman in a kitchen standing behind a row of supplement bottles on a marble counter" style="inset:0;background:linear-gradient(180deg,#4f3426 0%,#7d5a47 45%,#9c8577 70%,#e6e1dc 82%,#f1eeeb 100%)"></div>
  <div class="line light" style="top:156px;font-size:80px;text-shadow:0 2px 4px rgba(0,0,0,.35)">25% OFF</div>
  <div class="line light" style="top:234px;font-size:80px;text-shadow:0 2px 4px rgba(0,0,0,.35)">ALL SUPPLEMENTS</div>
  <div class="line light" style="top:311px;font-size:80px;text-shadow:0 2px 4px rgba(0,0,0,.35)">SPRING DETOX</div>
  <div class="line light" style="top:392px;font-size:80px;text-shadow:0 2px 4px rgba(0,0,0,.35)">SALE!</div>
</section>

<!-- Post 4 -->
<section class="post col-b row-2">
  <div class="line hot" style="top:28px;font-size:141px">25% OFF</div>
  <div class="line rose" style="top:162px;font-size:97px">SPRING DETOX</div>
  <div class="products" role="img" aria-label="Two supplement bottles" style="left:15px;top:252px;width:160px;height:132px"></div>
  <div class="line hot" style="top:257px;font-size:97px;left:175px;right:167px">SALE</div>
  <div class="products" role="img" aria-label="Two supplement bottles" style="left:327px;top:252px;width:167px;height:132px"></div>
  <div class="rule" style="left:0;width:494px;top:385px;height:4px"></div>
  <div class="line hot" style="top:404px;font-size:106px">SPRING RESET</div>
  <div class="line rose" style="top:500px;font-size:97px">SUMME READY</div>
</section>

<!-- Post 5 -->
<section class="post col-a row-3">
  <svg class="tri" width="494" height="617" viewBox="0 0 494 617" aria-hidden="true">
    <polygon points="0,0 313,0 0,290" fill="var(--rose)"/>
    <polygon points="494,513 494,617 379,617" fill="var(--rose)"/>
  </svg>
  <div class="line light left-align" style="left:20px;top:12px;font-size:112px">25</div>
  <div class="line light left-align" style="left:140px;top:20px;font-size:66px">%</div>
  <div class="line light left-align" style="left:142px;top:69px;font-size:54px">OFF</div>
  <div class="products" role="img" aria-label="Four supplement bottles in a row" style="left:207px;top:91px;width:260px;height:104px"></div>
  <div class="line hot right-align" style="right:27px;top:203px;font-size:87px">EVERYTHING</div>
  <div class="line rose left-align" style="left:30px;top:343px;font-size:87px">MOTHER’S DAY</div>
  <div class="line hot left-align" style="left:30px;top:423px;font-size:87px">SPRING DETOX</div>
  <div class="line rose left-align" style="left:30px;top:501px;font-size:87px">SALE</div>
  <div class="rule" style="left:160px;width:300px;top:539px;height:4px;background:var(--rose)"></div>
</section>

<!-- Post 6 -->
<section class="post col-b row-3" style="background:var(--blush)">
  <div class="line hot" style="top:45px;font-size:87px">25% OFF</div>
  <div class="line rose" style="top:131px;font-size:97px">MOTHER’S DAY</div>
  <div class="line hot" style="top:219px;font-size:97px">SALE</div>
  <div class="products" role="img" aria-label="Four supplement bottles arranged in perspective" style="left:53px;top:304px;width:372px;height:193px"></div>
  <div class="block" style="left:11px;top:497px;width:483px;height:78px;background:var(--hot);border-radius:39px"></div>
  <div class="line light round" style="top:514px;font-size:42px">Feel Amazing Again!</div>
</section>

<!-- Post 7 -->
<section class="post col-a row-4">
  <div class="photo" role="img" aria-label="Smiling woman in a white top standing in a kitchen behind a row of supplement bottles" style="left:0;top:18px;width:250px;height:273px;border-radius:0 120px 0 0;background:linear-gradient(180deg,#5a4034 0%,#8a6e60 55%,#d8d2cd 85%,#efebe8 100%)"></div>
  <div class="block" style="left:0;top:291px;width:250px;height:293px;background:var(--hot);border-radius:0 0 160px 0"></div>
  <div class="line light heavy left-align" style="left:0;width:210px;top:342px;font-size:40px;text-align:center">REFRESH</div>
  <div class="line light heavy left-align" style="left:0;width:210px;top:399px;font-size:40px;text-align:center">YOUR</div>
  <div class="line light heavy left-align" style="left:0;width:210px;top:456px;font-size:40px;text-align:center">BODY</div>
  <div class="line hot left-align" style="left:264px;top:66px;font-size:155px">25</div>
  <div class="line hot left-align" style="left:399px;top:66px;font-size:76px">%</div>
  <div class="line hot left-align" style="left:401px;top:143px;font-size:54px">OFF</div>
  <div class="line rose" style="left:250px;right:0;top:253px;font-size:68px">MOTHER’S</div>
  <div class="line hot" style="left:250px;right:0;top:327px;font-size:106px">DAY</div>
  <div class="line hot" style="left:250px;right:0;top:426px;font-size:136px">SALE</div>
</section>

<!-- Post 8 -->
<section class="post col-b row-4">
  <div class="line hot wide" style="top:38px;font-size:56px;letter-spacing:8px">25% OFF</div>
  <div class="line rose" style="top:118px;font-size:70px">SPRING DETOX SALE</div>
  <div class="products" role="img" aria-label="Four supplement bottles in a row" style="left:80px;top:196px;width:331px;height:135px"></div>
  <div class="line hot wide" style="top:309px;font-size:90px">SPRING</div>
  <div class="line hot wide" style="top:413px;font-size:84px">CLEANSE</div>
  <div class="line rose" style="top:519px;font-size:87px">SUMMER GLOW</div>
</section>

<!-- Post 9 -->
<section class="post col-a row-5">
  <div class="block" style="left:0;top:0;width:294px;height:203px;background:var(--rose)"></div>
  <div class="line light left-align" style="left:18px;top:16px;font-size:155px">25</div>
  <div class="line light left-align" style="left:183px;top:34px;font-size:76px">%</div>
  <div class="line light left-align" style="left:185px;top:112px;font-size:68px">OFF</div>
  <div class="line hot" style="left:294px;right:0;top:40px;font-size:53px">MOTHER’S</div>
  <div class="line hot" style="left:294px;right:0;top:90px;font-size:53px">DAY</div>
  <div class="line hot" style="left:294px;right:0;top:141px;font-size:53px">SALE</div>
  <div class="block" style="left:294px;top:203px;width:200px;height:414px;background:var(--hot)"></div>
  <div class="block" style="left:394px;top:395px;width:0;height:0">
    <div style="position:absolute;left:-121px;top:-72px;width:242px;transform:rotate(-90deg);transform-origin:121px 72px;line-height:1;font-family:'Bebas Neue',sans-serif;color:var(--white);white-space:nowrap">
      <div style="font-size:139px;height:100px;line-height:0.8">SHINE</div>
      <div style="font-size:58px;line-height:0.8;margin-top:-2px">THIS SUMMER</div>
    </div>
  </div>
  <div class="line hot left-align" style="left:18px;top:229px;font-size:116px">DETOX</div>
  <div class="line hot left-align" style="left:18px;top:331px;font-size:48px">THIS</div>
  <div class="line rose left-align" style="left:14px;top:365px;font-size:106px">SPRING</div>
  <div class="products" role="img" aria-label="Four supplement bottles arranged in perspective" style="left:14px;top:471px;width:261px;height:135px"></div>
</section>

<!-- Post 10 -->
<section class="post col-b row-5">
  <div class="line rose" style="top:9px;font-size:155px">25%OFF</div>
  <div class="line hot" style="top:146px;font-size:68px">MOTHER’S DAY SALE</div>
  <div class="block" style="left:134px;top:241px;width:230px;height:230px;border-radius:50%;background:var(--blush)"></div>
  <div class="products" role="img" aria-label="Four supplement bottles in a row" style="left:57px;top:254px;width:381px;height:163px;background:linear-gradient(180deg,rgba(247,246,248,.95),rgba(220,218,222,.95))"></div>
  <div class="line rose round" style="top:448px;font-size:57px;font-weight:600">Spring Detox</div>
  <div class="line hot round" style="top:528px;font-size:42px;font-weight:600">for a Summer Body</div>
</section>

</body>
</html>
```